Pull Up Banner - Recruitment Company

We would like a design for a pull up banner.

For context: we are a recruitment business. We specialise in helping people in healthcare industry to find jobs in Australia.

I have come up with several ideas and text for the banner. Feel free to use the following as you see appropriate:

- Our logo (see attached)
- 'Healthcare Recruitment Agency'
- Some sort of imagine / cartoon of medical professionals (ie. doctor, nurse, physiotherapist, speech pathologist). A cartoon is more friendly than committing to a photo
- 'Empowering your next career move'
- 'Discover tailored opportunities based on your career preferences'
- Dot points (allied health, nursing, medical imaging)
- Contact info at the bottom including our website (www.quellastaffing.com.au, our Instagram handle @quellastaffing, Mobile: XXXX XXX XXX. The title section for contact information could be 'Get in touch:'

Feel free to submit a couple of designs and we can merge aspects that look good on your designs and find the perfect fit.
Thank you
Updates

Hello,

Thank you for your initial submissions to this project. I appreciate the time you've invested.

After reviewing the first attempt, I'd like to share some feedback and initial observations:

- Professionalism and engagement: Is the overall appearance of the banner professional? It's crucial that we have a high-quality design as this will represent our business.

- Image selection: The image (whether cartoon or real people) appears quite generic. Please consider submitting the banner with a few different photos in the middle for us to choose from. Ensure the image is a good fit and not simply a generic stock photo.

- Contact section: Kindly remove the phone number; we no longer wish to include it on the banner. Instead, please include our website (www.quellastaffing.com.au) and Instagram handle (@quellastaffing).

- Color scheme: White, black, and red/pink are preferred, or alternatively, blue. However, please avoid incorporating too many different colors as it may detract from the professional appearance.

We will be printing the design on a banner and require it to look professional and engaging.

Thank you once again for your submissions. I hope the feedback provided above is helpful.

Warm regards,

Target Market(s)

Allied Health Australia

Font styles to use
Serif

Colors
0054AA
0677BA
7BADD7
CADEEF
E8F1F8
0094D4
00A9DD
6FCCEA
C7EBF8
E9F6FB
EB3D1F
EC4F4E
F09395
F8D3D4
FCEDEE

```html
<!DOCTYPE html>
<html lang="en">
<head>
<meta charset="utf-8">
<title>Quella Staffing – Pull Up Banner</title>
<link rel="stylesheet" href="https://fonts.googleapis.com/css2?family=Poppins:wght@300;400;500;600;700;800&display=swap">
<style>
  :root{
    --royal:#0b179f;
    --navy:#0c1169;
    --band:#3444d8;
    --sky:#6f9ff0;
    --accent:#1e88e5;
    --pill:#2196f3;
    --ink:#2b2b2b;
    --white:#ffffff;
    --art-light:#a9b8ee;
    --art-mid:#6d80d8;
  }
  *{margin:0;padding:0;box-sizing:border-box;}
  html,body{width:1200px;height:2400px;overflow:hidden;background:var(--white);}
  body{font-family:"Poppins",sans-serif;}
  .banner{position:relative;width:1200px;height:2400px;overflow:hidden;}
  .backdrop{position:absolute;inset:0;}
  .brand{position:absolute;top:95px;left:0;width:100%;text-align:center;color:var(--white);}
  .brand-name{font-size:118px;font-weight:700;letter-spacing:8px;line-height:1;}
  .brand-sub{font-size:34px;font-weight:700;letter-spacing:12px;margin-top:18px;line-height:1;}
  .headline{position:absolute;top:318px;left:0;width:100%;text-align:center;font-weight:800;line-height:108px;letter-spacing:-3px;color:var(--white);}
  .headline .lead{color:var(--sky);font-size:112px;}
  .headline .main{font-size:124px;display:block;}
  .tagline{position:absolute;top:1598px;left:0;width:100%;text-align:center;color:var(--ink);line-height:82px;}
  .tagline .soft{font-size:80px;font-weight:400;letter-spacing:-2px;display:block;}
  .tagline .strong{font-size:82px;font-weight:800;letter-spacing:-2px;display:block;}
  .discover{position:absolute;top:1760px;left:0;width:100%;text-align:center;color:var(--accent);font-size:46px;font-weight:600;letter-spacing:20px;}
  .offer{position:absolute;top:1828px;left:0;width:100%;text-align:center;color:var(--ink);font-size:48px;font-weight:600;line-height:58px;letter-spacing:-0.5px;}
  .sectors{position:absolute;top:1990px;left:100px;right:100px;display:flex;justify-content:center;align-items:flex-end;}
  .sector{display:flex;flex-direction:column;align-items:center;padding:0 42px;}
  .sector + .sector{border-left:3px solid #d7d7d7;}
  .sector svg{width:76px;height:70px;margin-bottom:8px;}
  .sector-label{font-size:38px;font-weight:500;color:var(--ink);white-space:nowrap;}
  .site{position:absolute;top:2140px;left:110px;right:110px;height:96px;border-radius:22px;background:var(--pill);color:var(--white);display:flex;align-items:center;justify-content:center;font-size:46px;font-weight:700;letter-spacing:3px;}
  .social{position:absolute;top:2250px;left:0;width:100%;display:flex;justify-content:center;align-items:center;gap:14px;font-size:46px;font-weight:300;color:var(--ink);}
  .social .dot{width:34px;height:34px;border-radius:50%;background:#e4405f;display:inline-block;}
  .social strong{font-weight:400;}
</style>
</head>
<body>
<main class="banner">
  <svg class="backdrop" width="1200" height="2400" viewBox="0 0 1200 2400">
    <defs>
      <linearGradient id="artTone" x1="0" y1="0" x2="1" y2="1">
        <stop offset="0" stop-color="var(--art-light)"/>
        <stop offset="1" stop-color="var(--art-mid)"/>
      </linearGradient>
    </defs>
    <rect width="1200" height="2400" fill="var(--royal)"/>
    <polygon points="1200,618 1200,1164 0,1700 0,1055" fill="var(--band)"/>
    <polygon points="0,645 560,851 0,1055" fill="var(--navy)"/>
    <polygon points="1200,1164 1200,2400 0,2400 0,1700" fill="var(--navy)"/>
    <polygon points="0,1645 760,1382 1200,1573 1200,2400 0,2400" fill="var(--white)"/>
    <g role="img" aria-label="Isometric illustration of a doctor and a radiographer at a control desk beside a patient lying in a medical imaging scanner">
      <polygon points="230,700 1000,720 1120,1180 620,1560 120,1500 90,1000" fill="url(#artTone)" opacity="0.55"/>
    </g>
  </svg>

  <header class="brand">
    <div class="brand-name">QUELLA</div>
    <div class="brand-sub">STAFFING</div>
  </header>

  <h1 class="headline">
    <span class="lead">HEALTHCARE</span>
    <span class="main">RECRUITMENT</span>
    <span class="main">AGENCY</span>
  </h1>

  <h2 class="tagline">
    <span class="soft">EMPOWERING YOUR</span>
    <span class="strong">NEXT CAREER MOVE</span>
  </h2>

  <p class="discover">DISCOVER</p>
  <p class="offer">tailored opportunities based on your<br>career preferences</p>

  <ul class="sectors">
    <li class="sector">
      <svg viewBox="0 0 76 70" aria-hidden="true">
        <path d="M38 44 C20 32 14 24 14 16 C14 9 19 5 25 5 C30 5 35 8 38 13 C41 8 46 5 51 5 C57 5 62 9 62 16 C62 24 56 32 38 44Z" fill="var(--royal)"/>
        <polyline points="4,22 24,22 30,12 36,32 42,18 46,22 72,22" fill="none" stroke="var(--white)" stroke-width="3"/>
        <path d="M8 56 L28 50 L46 52 L64 44 L68 50 L46 64 L8 64Z" fill="var(--accent)"/>
      </svg>
      <span class="sector-label">Allied health</span>
    </li>
    <li class="sector">
      <svg viewBox="0 0 76 70" aria-hidden="true">
        <rect x="26" y="2" width="24" height="10" rx="3" fill="var(--royal)"/>
        <circle cx="38" cy="24" r="12" fill="var(--royal)"/>
        <path d="M14 68 C14 48 24 40 38 40 C52 40 62 48 62 68Z" fill="var(--royal)"/>
        <rect x="34" y="48" width="8" height="16" fill="var(--white)"/>
        <rect x="30" y="52" width="16" height="8" fill="var(--white)"/>
      </svg>
      <span class="sector-label">Nursing</span>
    </li>
    <li class="sector">
      <svg viewBox="0 0 76 70" aria-hidden="true">
        <path d="M14 34 A24 24 0 0 1 62 34" fill="none" stroke="var(--royal)" stroke-width="9"/>
        <rect x="10" y="32" width="56" height="10" rx="3" fill="var(--accent)"/>
        <rect x="20" y="46" width="44" height="8" fill="var(--royal)"/>
        <rect x="52" y="54" width="6" height="14" fill="var(--royal)"/>
      </svg>
      <span class="sector-label">Medical imaging</span>
    </li>
  </ul>

  <div class="site">www.quellastaffing.com.au</div>
  <p class="social">Follow us at <span class="dot" aria-hidden="true"></span><strong>@quellastaffing</strong></p>
</main>
</body>
</html>
```